Business Card Design for Occupational Medicine Start Up Company

We need to design a professional business card. We are a healthcare company providing occupational medicine services to blue collar industries. We are professional, efficient and high quality service providers.

Target Market(s)

Blue Collar Industry: Shipbuilding, Ports, Trucking Companies; The Executives and Safety Officers for these companies

Industry/Entity Type

Healthcare

Contact Information for Business Card

Logo, Name, Title, Email, Phone

Other font styles liked:
• Please match our Brand Guide

Requirements
Must have
• Our Company Colors and Logo

```html
<!DOCTYPE html>
<html lang="en">
<head>
<meta charset="utf-8">
<title>ShiftWell Business Card</title>
<link rel="stylesheet" href="https://fonts.googleapis.com/css2?family=Montserrat:wght@500&family=Oswald:wght@600&family=Roboto:wght@400&display=swap">
<style>
  :root {
    --stage: #3a3a3c;
    --card: #141415;
    --card-edge: #1d1d1f;
    --brand-blue: #2a3fb0;
    --brand-sky: #2b8fd6;
    --brand-amber: #f0a531;
    --silver: #b9b9bc;
    --text-light: #e8e8ea;
    --text-muted: #c9c9cc;
  }
  * { margin: 0; padding: 0; box-sizing: border-box; }
  html, body {
    width: 1200px; height: 900px; overflow: hidden;
    background: radial-gradient(ellipse at 60% 55%, #4a4a4d 0%, var(--stage) 55%, #232325 100%);
  }
  .canvas { position: relative; width: 1200px; height: 900px; }
  .card {
    position: absolute; width: 525px; height: 300px;
    background: linear-gradient(150deg, var(--card-edge), var(--card));
    border-radius: 26px;
    box-shadow: 0 18px 40px rgba(0,0,0,.55), 0 4px 0 #0b0b0c;
  }
  .card--front { left: 120px; top: 300px; }
  .card--back { left: 555px; top: 120px; }

  .brand-lockup {
    position: absolute; left: 0; right: 0; top: 50%;
    transform: translateY(-50%);
    display: flex; align-items: center; justify-content: center; gap: 16px;
  }
  .brand-dot {
    width: 34px; height: 34px; border-radius: 50%;
    background: var(--brand-sky);
  }
  .brand-name {
    font-family: "Montserrat", sans-serif; font-weight: 500;
    font-size: 38px; letter-spacing: 4px; color: var(--silver);
  }

  .identity {
    position: absolute; left: 70px; top: 108px; text-align: right; width: 190px;
  }
  .identity__name {
    font-family: "Oswald", sans-serif; font-weight: 600;
    font-size: 30px; line-height: 1; color: var(--brand-blue);
    text-transform: uppercase; letter-spacing: .5px; white-space: nowrap;
  }
  .identity__title {
    font-family: "Roboto", sans-serif; font-size: 14px;
    color: var(--text-muted); margin-top: 6px;
  }
  .divider {
    position: absolute; left: 275px; top: 112px;
    width: 2px; height: 66px; background: var(--brand-amber);
  }
  .contacts {
    position: absolute; left: 292px; top: 110px; list-style: none;
    font-family: "Roboto", sans-serif; font-size: 15px; color: var(--text-light);
  }
  .contacts li { display: flex; align-items: center; gap: 7px; height: 23px; }
  .contacts svg { width: 11px; height: 11px; fill: var(--brand-blue); flex: none; }
</style>
</head>
<body>
<main class="canvas">
  <section class="card card--front" aria-label="Card front">
    <div class="brand-lockup">
      <span class="brand-dot"></span>
      <span class="brand-name">SHIFTWELL</span>
    </div>
  </section>

  <section class="card card--back" aria-label="Card back">
    <div class="identity">
      <p class="identity__name">Marcus Ellery</p>
      <p class="identity__title">Director</p>
    </div>
    <span class="divider"></span>
    <ul class="contacts">
      <li>
        <svg viewBox="0 0 24 24" aria-hidden="true"><path d="M6.6 10.8a15.1 15.1 0 0 0 6.6 6.6l2.2-2.2a1 1 0 0 1 1-.25 11.4 11.4 0 0 0 3.6.57 1 1 0 0 1 1 1V20a1 1 0 0 1-1 1A17 17 0 0 1 3 4a1 1 0 0 1 1-1h3.5a1 1 0 0 1 1 1c0 1.25.2 2.45.57 3.57a1 1 0 0 1-.25 1z"/></svg>
        (555) 014 2290
      </li>
      <li>
        <svg viewBox="0 0 24 24" aria-hidden="true"><path d="M2 5h20v14H2zm2 2v.5l8 5 8-5V7z"/></svg>
        hello@shiftwellhealth.com
      </li>
      <li>
        <svg viewBox="0 0 24 24" aria-hidden="true"><path d="M12 2a10 10 0 1 0 0 20 10 10 0 0 0 0-20zm0 2c.9 1.2 1.6 2.6 2 4h-4c.4-1.4 1.1-2.8 2-4zM4.3 14a8 8 0 0 1 0-4h3.4a16 16 0 0 0 0 4zm5.7 0a14 14 0 0 1 0-4h4a14 14 0 0 1 0 4zm6.3 0a16 16 0 0 0 0-4h3.4a8 8 0 0 1 0 4z"/></svg>
        www.shiftwellhealth.com
      </li>
    </ul>
  </section>
</main>
</body>
</html>
```